Business Card Design for Varomir Facility Services

We are looking for a Business Card Design for the Company "Varomir Facility Services."
Front side:
- Company Logo (small)
- Company Name, address, pohone, website and personal data.
- white background, for text e.g. company colors (blue or green like in the logo)
Please use following data:
Company data:
Varomir Facility Services Kostelac
Birkenhaldweg 14
6330 Cham
www.varomir-fs.ch
Person data:
Tarik Kostelac
Geschäftsführer
+41 76 519 47 83
info@varomir-fs.ch
Back side:
could be colored in blue or green
please use a big logo sing and some smaller icons to say what is all beeing offered in facility services, like cleaning, maintenance cleaning
industrial cleaning, caretaking, gardening, disposal. There is no need for everyone of the icons if there are similar or an icon is standing for more of them.
colors to use:
blue: HEX 246BB0
green: HEX 52B33E

```html
<!DOCTYPE html>
<html lang="de">
<head>
<meta charset="utf-8">
<title>Varomir Facility Services – Business Card</title>
<link rel="stylesheet" href="https://fonts.googleapis.com/css2?family=Montserrat:wght@500;700&family=Lato:wght@400&display=swap">
<style>
  :root {
    --blue: #246bb0;
    --green: #52b33e;
    --card-green: #21b24f;
    --ink: #5a5a5a;
    --paper: #ffffff;
    --stage: #3a3a3a;
    --icon-blue: #2f6fc0;
  }
  * { box-sizing: border-box; margin: 0; padding: 0; }
  html, body { width: 1200px; height: 905px; overflow: hidden; }
  body {
    background: var(--stage);
    font-family: "Montserrat", sans-serif;
    position: relative;
  }
  .card {
    position: absolute;
    left: 280px;
    width: 640px;
    height: 366px;
    border-radius: 18px;
    overflow: hidden;
    box-shadow: 0 14px 30px rgba(0,0,0,.45);
  }
  /* back side */
  .card-back { top: 60px; background: var(--card-green); color: #fff; }
  .back-brand {
    position: absolute; top: 70px; left: 0; right: 0;
    display: flex; align-items: center; justify-content: center; gap: 16px;
  }
  .back-brand .mark { width: 34px; height: 34px; border-radius: 50%; background: #fff; }
  .back-brand .name {
    font-weight: 700; font-size: 30px; letter-spacing: 1px; text-transform: uppercase; color: #fff;
  }
  .services {
    position: absolute; left: 30px; right: 30px; bottom: 60px;
    display: flex; justify-content: space-between; list-style: none;
  }
  .service { width: 110px; text-align: center; font-family: "Lato", sans-serif; font-size: 14px; }
  .service .pictogram {
    display: block; width: 46px; height: 46px; margin: 0 auto 12px; border-radius: 50%;
    background: radial-gradient(circle at 40% 35%, #5b8fd6, var(--icon-blue));
  }
  /* front side */
  .card-front { top: 480px; background: var(--paper); }
  .front-brand {
    position: absolute; top: 34px; right: 36px;
    display: flex; align-items: center; gap: 10px;
  }
  .front-brand .mark { width: 18px; height: 18px; border-radius: 50%; background: var(--green); }
  .front-brand .name { font-weight: 700; font-size: 17px; color: var(--blue); text-transform: uppercase; letter-spacing: .5px; }
  .rule { position: absolute; height: 1.5px; background: var(--blue); right: 36px; }
  .rule-top { top: 150px; left: 300px; }
  .rule-mid { top: 232px; left: 420px; }
  .accent { position: absolute; left: 0; top: 178px; width: 10px; height: 40px; background: var(--green); }
  .band { position: absolute; left: 0; right: 0; bottom: 0; height: 22px; background: var(--blue); }
  .person { position: absolute; left: 40px; top: 128px; }
  .person .full-name { font-weight: 700; font-size: 20px; color: var(--blue); text-transform: uppercase; }
  .person .role { font-weight: 500; font-size: 15px; color: var(--ink); margin-top: 4px; }
  .contact-line {
    display: flex; align-items: center; gap: 8px;
    font-weight: 500; font-size: 14px; color: var(--ink);
  }
  .contact-line .sep { color: var(--green); margin: 0 6px; }
  .contact-line svg { width: 14px; height: 14px; flex: none; }
  .person .contact-line { margin-top: 12px; }
  .company { position: absolute; left: 40px; top: 220px; }
  .company .legal-name { font-weight: 700; font-size: 17px; color: var(--green); text-transform: uppercase; margin-bottom: 10px; }
</style>
</head>
<body>

<section class="card card-back" aria-label="Back side">
  <div class="back-brand">
    <span class="mark"></span>
    <span class="name">Varomir Facility Services</span>
  </div>
  <ul class="services">
    <li class="service"><span class="pictogram" role="img" aria-label="Pictogram of maintenance cleaning"></span>Maintenance cleaning</li>
    <li class="service"><span class="pictogram" role="img" aria-label="Pictogram of industrial cleaning"></span>Industrial cleaning</li>
    <li class="service"><span class="pictogram" role="img" aria-label="Pictogram of caretaking"></span>Caretaking</li>
    <li class="service"><span class="pictogram" role="img" aria-label="Pictogram of gardening"></span>Gardening</li>
    <li class="service"><span class="pictogram" role="img" aria-label="Pictogram of disposal"></span>Disposal</li>
  </ul>
</section>

<section class="card card-front" aria-label="Front side">
  <div class="front-brand">
    <span class="mark"></span>
    <span class="name">Varomir Facility Services</span>
  </div>
  <div class="rule rule-top"></div>
  <div class="rule rule-mid"></div>
  <div class="accent"></div>

  <div class="person">
    <p class="full-name">Tarik Kostelac</p>
    <p class="role">Geschäftsführer</p>
    <p class="contact-line">
      <svg viewBox="0 0 24 24" fill="var(--blue)" aria-hidden="true"><path d="M6.6 10.8a15 15 0 0 0 6.6 6.6l2.2-2.2a1 1 0 0 1 1-.25 11.4 11.4 0 0 0 3.6.57 1 1 0 0 1 1 1V20a1 1 0 0 1-1 1A17 17 0 0 1 3 4a1 1 0 0 1 1-1h3.5a1 1 0 0 1 1 1c0 1.25.2 2.45.57 3.57a1 1 0 0 1-.25 1z"/></svg>
      +41 76 519 47 83
      <span class="sep">|</span>
      <svg viewBox="0 0 24 24" aria-hidden="true"><rect x="2" y="5" width="20" height="14" rx="1.5" fill="var(--blue)"/><path d="M3 6l9 7 9-7" stroke="#fff" stroke-width="1.8" fill="none"/></svg>
      info@varomir-fs.ch
    </p>
  </div>

  <div class="company">
    <p class="legal-name">Varomir Facility Services Kostelac</p>
    <p class="contact-line">
      <svg viewBox="0 0 24 24" aria-hidden="true"><circle cx="12" cy="12" r="10" fill="var(--green)"/><path d="M2 12h20M12 2c3 3 3 17 0 20M12 2c-3 3-3 17 0 20" stroke="#fff" stroke-width="1.4" fill="none"/></svg>
      www.varomir-fs.ch
      <span class="sep">|</span>
      <svg viewBox="0 0 24 24" aria-hidden="true"><path d="M12 2a7 7 0 0 0-7 7c0 5 7 13 7 13s7-8 7-13a7 7 0 0 0-7-7z" fill="var(--green)"/><circle cx="12" cy="9" r="2.6" fill="#fff"/></svg>
      Birkenhaldweg 14 6330 Cham
    </p>
  </div>

  <div class="band"></div>
</section>

</body>
</html>
```